Family Values Statement Image

I have created a statement of values for my family. Our last name is Pilwothy, and we are using those letters as an acronym. I would like an image with these words and letters with a tree with deep roots, where the roots are the focal point.

A - All In
N - Never Settle
D - Dependable
E - Enthusiastic
R - Repair
E - Enduring
G - Gushy Hearted
G - Gratitudes

Note that "gratitudes" is intentionally misspelled.

• On further reflection, I am interested in the words being much more prominent than the tree. In fact, the tree could be quite small or even just a watermark behind the words.

```html
<!DOCTYPE html>
<html lang="en">
<head>
<meta charset="utf-8">
<title>Pilwothy Family Values</title>
<link rel="stylesheet" href="https://fonts.googleapis.com/css2?family=Alfa+Slab+One&family=Anton&family=Archivo:wdth,wght@125,900&family=Montserrat:wght@600&family=Mrs+Saint+Delafield&family=Oswald:wght@600&family=Ultra&display=swap">
<style>
  :root {
    --poster-black: #050505;
    --value-grey: #8c8c8c;
    --value-light: #e2e2e2;
    --value-mid: #b9b9b9;
    --pill-white: #f4f4f4;
    --pill-shade: #c9c9c9;
    --ink-black: #070707;
    --label-grey: #d0d0d0;
    --script-grey: #7a7a7a;
    --tree-light: #9a9a9a;
    --tree-dark: #3a3a3a;
  }
  html, body {
    margin: 0;
    padding: 0;
    width: 1122px;
    height: 1200px;
    overflow: hidden;
    background: var(--poster-black);
  }
  .poster {
    position: relative;
    width: 1122px;
    height: 1200px;
    background: var(--poster-black);
  }
  .poster svg { display: block; }
  .value-wide { font-family: "Archivo", sans-serif; font-weight: 900; font-stretch: 125%; fill: var(--value-grey); }
  .value-western { font-family: "Ultra", serif; fill: var(--value-light); }
  .value-condensed { font-family: "Anton", sans-serif; fill: var(--value-grey); }
  .value-slab { font-family: "Alfa Slab One", serif; fill: var(--value-mid); }
  .value-boxed { font-family: "Oswald", sans-serif; font-weight: 600; fill: var(--ink-black); }
  .pill { fill: url(#pillShade); stroke: var(--ink-black); stroke-width: 4; }
  .heart { fill: var(--value-grey); }
  .family-label { font-family: "Montserrat", sans-serif; font-weight: 600; fill: var(--label-grey); letter-spacing: 1px; }
  .family-name { font-family: "Mrs Saint Delafield", cursive; fill: var(--script-grey); }
</style>
</head>
<body>
<main class="poster">
  <svg width="1122" height="1200" viewBox="0 0 1122 1200" xmlns="http://www.w3.org/2000/svg">
    <defs>
      <linearGradient id="pillShade" x1="0" y1="0" x2="1" y2="0">
        <stop offset="0" stop-color="#f6f6f6"/>
        <stop offset="1" stop-color="#c6c6c6"/>
      </linearGradient>
      <linearGradient id="treeShade" x1="0" y1="0" x2="0" y2="1">
        <stop offset="0" stop-color="#a8a8a8"/>
        <stop offset="1" stop-color="#3a3a3a"/>
      </linearGradient>
    </defs>

    <g class="family-heading">
      <text class="family-label" transform="translate(112 447) rotate(-90)" font-size="34" textLength="340" lengthAdjust="spacingAndGlyphs">FAMILY VALUES</text>
      <text class="family-name" transform="translate(170 600) rotate(-78)" font-size="92" textLength="360" lengthAdjust="spacingAndGlyphs">Pilwothy</text>
    </g>

    <rect class="tree-mark" role="img" aria-label="Small illustrated tree with leafy crown and deep roots" x="0" y="850" width="243" height="350" rx="60" fill="url(#treeShade)" opacity="0.8"/>

    <g class="value-stack">
      <path class="heart" d="M820 104 C808 94 798 86 798 77 C798 70 803 66 809 66 C814 66 818 69 820 73 C822 69 826 66 831 66 C837 66 842 70 842 77 C842 86 832 94 820 104 Z"/>
      <text class="value-wide" x="290" y="202" font-size="128" textLength="720" lengthAdjust="spacingAndGlyphs">ALL IN</text>

      <text class="value-western" x="297" y="347" font-size="132" textLength="713" lengthAdjust="spacingAndGlyphs">Never Settle</text>

      <text class="value-condensed" x="300" y="490" font-size="150" textLength="712" lengthAdjust="spacingAndGlyphs">DEPENDABLE</text>

      <rect class="pill" x="297" y="503" width="716" height="106" rx="22"/>
      <text class="value-boxed" x="312" y="594" font-size="108" textLength="686" lengthAdjust="spacingAndGlyphs">ENTHUSIASTIC</text>

      <text class="value-wide" x="285" y="730" font-size="124" textLength="730" lengthAdjust="spacingAndGlyphs">REPAIR</text>

      <text class="value-slab" x="295" y="903" font-size="170" textLength="713" lengthAdjust="spacingAndGlyphs" transform="translate(0 -270) scale(1 1.3)" style="transform-origin:0 0">ENDURING</text>

      <rect class="pill" x="297" y="912" width="700" height="116" rx="24"/>
      <text class="value-boxed" x="312" y="1013" font-size="116" textLength="670" lengthAdjust="spacingAndGlyphs">GUSHY HEARTED</text>

      <text class="value-condensed" x="285" y="1156" font-size="150" textLength="705" lengthAdjust="spacingAndGlyphs">GRADTITUDES</text>
    </g>
  </svg>
</main>
</body>
</html>
```